Podcast cover for Zorvo

Hi
I am after a podcast cover for Zorvo.The image will have to meet their guidelines
Check out images on Zorvo podcast section if you are not sure. Here is what they say about specs required.
-------------------Quenby Description below this line ----------
Cover art must be in the JPEG or PNG file formats and in the RGB color space with a minimum size of 1400 x 1400 pixels and a maximum size of 2048 x 2048 pixels. Note that these requirements are different from the standard RSS image tag specification.
Potential subscribers will see your cover art in varying sizes depending on the device they’re using. Make sure your design is effective at both its original size and at thumbnail size.
-------------------Quenby Description above this line ----------

I will try to convey what the show is about to assist in prompting some ideas.

I am sure you have heard the expression “connecting the dots”
My podcast is a variation of this.

My show is called “sowing distant lanterns”
Just those three words to appear on the image. Remember they must be clearly readable at the size that Zorvo will scale them to. (see above)

The idea behind the show is that we can create our dots and as we move through life we reach out and connect to those dots.

We are looking at the categories of Mysticism – Spirituality – Personal growth - Success

The image should reflect the above categories (absolutely not ‘godly’) and no cliché images of rising suns – halos – rainbows etc

Dots might make up some part of the image or something that represents dots. Mountains - crashing waves - jungle - Think – Nature – connected to earth – spirituality.

Some personal background which may help with the design idea. I am 55 years old and have for most of my life been searching.
Why are we here – what is our role and how do we make this life a meaningful one.

Some months ago I travelled to Iquitos, in Peru (the most remote city on the planet.) I ended up meeting a shaman and taking part in a ceremony deep in the Amazon jungle.
As a result of this I found the answers my questions. Hence the podcast to relay my experience.

Ok thats the story what can you come up with :-)

```html
<!DOCTYPE html>
<html lang="en">
<head>
<meta charset="utf-8">
<title>Sowing Distant Lanterns — Podcast Cover</title>
<link rel="stylesheet" href="https://fonts.googleapis.com/css2?family=Anton&family=Bebas+Neue&display=swap">
<style>
  :root {
    --page: #ffffff;
    --navy-deep: #0b2f52;
    --navy: #123f6e;
    --navy-light: #2a5f94;
    --band: #071a33;
    --sky-blue: #3f74c4;
    --ice: #dfe9f7;
    --white: #ffffff;
  }
  html, body {
    margin: 0;
    padding: 0;
    width: 1200px;
    height: 1000px;
    overflow: hidden;
    background: var(--page);
  }
  .cover {
    display: block;
    width: 1200px;
    height: 1000px;
  }
  .title-main {
    font-family: "Anton", sans-serif;
    font-size: 300px;
  }
  .title-middle {
    font-family: "Bebas Neue", sans-serif;
    font-size: 150px;
  }
  .title-tall {
    font-family: "Bebas Neue", sans-serif;
    font-size: 410px;
  }
</style>
</head>
<body>
<svg class="cover" viewBox="0 0 1200 1000" xmlns="http://www.w3.org/2000/svg">
  <defs>
    <radialGradient id="burst-light" cx="0.33" cy="0.42" r="0.75">
      <stop offset="0" stop-color="#ffffff"/>
      <stop offset="0.16" stop-color="#eef3fb"/>
      <stop offset="0.42" stop-color="#8fb0de"/>
      <stop offset="0.7" stop-color="#3f6fb8"/>
      <stop offset="1" stop-color="#1d3f78"/>
    </radialGradient>
    <linearGradient id="band-fade" x1="0" y1="0" x2="1" y2="0">
      <stop offset="0" stop-color="#050f22"/>
      <stop offset="0.6" stop-color="#0b2a55"/>
      <stop offset="1" stop-color="#13407a"/>
    </linearGradient>
    <linearGradient id="title-fill" x1="0" y1="0" x2="0" y2="1">
      <stop offset="0" stop-color="var(--navy-light)"/>
      <stop offset="0.5" stop-color="var(--navy)"/>
      <stop offset="1" stop-color="var(--navy-deep)"/>
    </linearGradient>
    <filter id="title-glow" x="-10%" y="-20%" width="120%" height="140%">
      <feMorphology in="SourceAlpha" operator="dilate" radius="6" result="grown"/>
      <feGaussianBlur in="grown" stdDeviation="5" result="soft"/>
      <feFlood flood-color="#ffffff"/>
      <feComposite in2="soft" operator="in" result="halo"/>
      <feMerge>
        <feMergeNode in="halo"/>
        <feMergeNode in="SourceGraphic"/>
      </feMerge>
    </filter>
    <clipPath id="artboard">
      <rect x="127" y="18" width="951" height="952"/>
    </clipPath>
  </defs>

  <g clip-path="url(#artboard)">
    <rect class="burst-backdrop" x="127" y="18" width="951" height="952"
          fill="url(#burst-light)" role="img"
          aria-label="Abstract blue light burst with streaking rays, glowing dots and a white paint splash"/>
    <rect class="lower-band" x="127" y="712" width="951" height="165" fill="url(#band-fade)" opacity="0.95"/>
    <circle class="band-ring" cx="980" cy="790" r="80" fill="#0a2447" opacity="0.7"/>
  </g>

  <text class="title-main" x="180" y="345" textLength="835" lengthAdjust="spacingAndGlyphs"
        fill="url(#title-fill)" stroke="#ffffff" stroke-width="3" filter="url(#title-glow)">SOWING</text>

  <text class="title-middle" transform="translate(478 360) rotate(12)" x="0" y="105"
        textLength="310" lengthAdjust="spacingAndGlyphs" fill="var(--navy-deep)">DISTANT</text>

  <text class="title-tall" x="245" y="832" textLength="500" lengthAdjust="spacingAndGlyphs"
        fill="var(--white)" stroke="var(--navy-deep)" stroke-width="7" paint-order="stroke">LANTERNS</text>

  <g class="trailing-dots" fill="var(--white)" stroke="var(--navy-deep)" stroke-width="3">
    <circle cx="790" cy="812" r="19"/>
    <circle cx="842" cy="812" r="19"/>
    <circle cx="894" cy="812" r="19"/>
  </g>
</svg>
</body>
</html>
```